Sickle Cell Patient Flyer

I need this be appealing to families dealing with sickle cell disease. Both informative-introducing the idea that a stroke prevention program is not only easy for their children but necessary. Stroke is a risk to all with children with SCD.
I included a few info flyers from the Vessel Alliance and licensed to me photos I like. I am open to suggestions.
web address is brightpathwellbeing.net
Call to schedule 833-412-7086
TCD is a safe and accurate tool that makes stroke prevention possible for your SCD patients and family.
Risk is highest for SCD sufferers age 2 to 5. Protect your childs future.

Target Market(s)

Parents, families and medical professionals

Industry/Entity Type

Medical wellness

Font styles to use
Other font styles liked:
• something close to my logo font

Colors
0094D4
00A9DD
6FCCEA
C7EBF8
E9F6FB

Requirements
Nice to have
• pictures of kids (Children of color) pictures of Brains, kids happy with medical professionals
Should not have
• dark colors

```html
<!DOCTYPE html>
<html lang="en">
<head>
<meta charset="utf-8">
<title>Stroke Prevention for Children with Sickle Cell Disease</title>
<link href="https://fonts.googleapis.com/css2?family=Bangers&family=Montserrat:ital,wght@0,600;0,700;0,800;1,500;1,700;1,800&display=swap" rel="stylesheet">
<style>
  :root {
    --paper: #f5f6f7;
    --title-navy: #4a4f9f;
    --script-blue: #1f8fd6;
    --mint: #72c8a0;
    --sky: #55a3d6;
    --ring-navy: #3d4a93;
    --swoosh-blue: #1a8ad2;
    --swoosh-light: #d3ecf8;
    --deep-navy: #1d3c8c;
    --white: #ffffff;
    --stripe-1: #1e3d7a;
    --stripe-2: #6fcce9;
    --stripe-3: #e0587a;
    --stripe-4: #f2b3a6;
    --stripe-5: #f3c28a;
    --stripe-6: #514a80;
    --stripe-7: #8dcf8e;
  }
  * { margin: 0; padding: 0; box-sizing: border-box; }
  html, body { width: 848px; height: 1200px; overflow: hidden; background: var(--paper); }
  .flyer { position: relative; width: 848px; height: 1200px; background: var(--paper); font-family: "Montserrat", sans-serif; overflow: hidden; }

  .stripe { position: absolute; left: 0; width: 848px; height: 7px; display: flex; }
  .stripe span { flex: 1; }
  .stripe--top { top: 0; }
  .stripe--bottom { bottom: 0; }
  .stripe span:nth-child(7n+1) { background: var(--stripe-7); }
  .stripe span:nth-child(7n+2) { background: var(--stripe-1); }
  .stripe span:nth-child(7n+3) { background: var(--stripe-2); }
  .stripe span:nth-child(7n+4) { background: var(--stripe-3); }
  .stripe span:nth-child(7n+5) { background: var(--stripe-4); }
  .stripe span:nth-child(7n+6) { background: var(--stripe-5); }
  .stripe span:nth-child(7n+7) { background: var(--stripe-6); }

  .headline { position: absolute; left: 52px; top: 50px; }
  .headline__lead { font-weight: 800; color: var(--title-navy); font-size: 37px; line-height: 45px; letter-spacing: 0.2px; }
  .headline__accent { font-family: "Bangers", sans-serif; color: var(--script-blue); font-size: 50px; line-height: 52px; letter-spacing: 1px; margin-top: 6px; font-style: italic; }

  .brand { position: absolute; left: 540px; top: 92px; width: 270px; display: flex; align-items: center; gap: 12px; }
  .brand__dot { width: 30px; height: 30px; border-radius: 50%; background: var(--mint); flex: none; }
  .brand__name { font-weight: 800; color: var(--sky); font-size: 30px; line-height: 34px; }

  .feature { position: absolute; top: 329px; width: 331px; height: 100px; color: var(--white); font-weight: 700; font-size: 21px; line-height: 27px; text-align: center; padding-top: 34px; box-shadow: 0 12px 14px -10px rgba(0,0,0,0.18); }
  .feature--simple { left: 53px; background: var(--mint); }
  .feature--tcd { left: 463px; background: var(--sky); }
  .feature__badge { position: absolute; top: -48px; left: 50%; margin-left: -35px; width: 70px; height: 70px; border-radius: 50%; border: 5px solid var(--ring-navy); display: flex; align-items: center; justify-content: center; }
  .feature--simple .feature__badge { background: var(--mint); }
  .feature--tcd .feature__badge { background: var(--sky); }
  .feature__badge svg { width: 56px; height: 56px; }

  .hero { position: absolute; left: 0; top: 460px; width: 848px; height: 580px; }
  .hero__art { position: absolute; left: 0; top: 0; }
  .hero__brain { position: absolute; left: 318px; top: 18px; width: 222px; height: 190px; border-radius: 50% 50% 45% 45%; background: radial-gradient(ellipse at center, #dbe8f7 0%, rgba(219,232,247,0) 72%); }
  .hero__child { position: absolute; left: 320px; top: 60px; width: 360px; height: 508px; border-radius: 140px 140px 0 0; background: linear-gradient(180deg, #f7cf4a 0%, #f4bd1e 60%, #eeb116 100%); }

  .why-tag { position: absolute; left: 86px; top: 617px; width: 138px; height: 46px; background: var(--white); border: 3px solid var(--mint); border-radius: 24px 8px 24px 8px; font-weight: 800; font-style: italic; color: var(--mint); font-size: 33px; line-height: 40px; text-align: center; }
  .why-copy { position: absolute; left: 0; top: 682px; color: var(--white); font-weight: 700; font-style: italic; font-size: 17px; line-height: 21.2px; }
  .why-copy span { display: block; white-space: nowrap; }
  .age-label { position: absolute; left: 163px; top: 882px; color: var(--white); font-weight: 800; font-size: 26px; }
  .age-pill { position: absolute; left: 97px; top: 918px; width: 194px; height: 75px; background: var(--white); border: 3px solid var(--mint); border-radius: 34px 10px 34px 10px; text-align: center; color: var(--script-blue); }
  .age-pill__range { font-weight: 800; font-size: 38px; line-height: 40px; margin-top: 5px; }
  .age-pill__unit { font-style: italic; font-weight: 500; font-size: 20px; line-height: 22px; }

  .closing { position: absolute; left: 0; top: 1057px; width: 848px; text-align: center; font-style: italic; }
  .closing__line { color: var(--title-navy); font-weight: 500; font-size: 15.5px; letter-spacing: 0.1px; }
  .closing__cta { color: var(--script-blue); font-weight: 800; font-size: 22px; margin-top: 4px; }

  .footer { position: absolute; left: 0; top: 1148px; width: 848px; height: 45px; background: var(--sky); }
  .footer__call { position: absolute; left: 33px; top: 9px; font-family: "Bangers", sans-serif; color: var(--white); font-size: 23px; letter-spacing: 0.5px; font-style: italic; }
  .footer__arrow { position: absolute; left: 225px; top: 11px; }
  .footer__phone-box { position: absolute; left: 260px; top: 1133px; width: 328px; height: 60px; background: var(--mint); text-align: center; font-family: "Bangers", sans-serif; color: var(--deep-navy); font-size: 46px; line-height: 62px; letter-spacing: 1px; font-style: italic; }
  .footer__web { position: absolute; right: 30px; top: 13px; font-family: "Bangers", sans-serif; color: var(--white); font-size: 16px; letter-spacing: 0.8px; }
</style>
</head>
<body>
<main class="flyer">
  <div class="stripe stripe--top"><span></span><span></span><span></span><span></span><span></span><span></span><span></span><span></span><span></span><span></span><span></span><span></span><span></span><span></span></div>

  <header class="headline">
    <h1 class="headline__lead">Stroke Prevention<br>for Children with</h1>
    <p class="headline__accent">SICKLE CELL DISEASE<br>IS POSSIBLE!</p>
  </header>

  <div class="brand">
    <span class="brand__dot"></span>
    <span class="brand__name">Bright Path<br>Wellbeing</span>
  </div>

  <section class="feature feature--simple">
    <div class="feature__badge">
      <svg viewBox="0 0 56 56" fill="none" stroke="#fff" stroke-width="2.2" stroke-linecap="round">
        <circle cx="28" cy="22" r="4"/>
        <path d="M20 40 h16 M22 40 l3-10 h6 l3 10 M20 34 l6-3 M36 34 l-6-3"/>
        <path d="M19 15 a12 12 0 0 0 0 14 M37 15 a12 12 0 0 1 0 14"/>
      </svg>
    </div>
    Simple and Painless<br>Screening for Your Child.
  </section>

  <section class="feature feature--tcd">
    <div class="feature__badge">
      <svg viewBox="0 0 56 56" fill="none" stroke="#fff" stroke-width="2.2" stroke-linecap="round" stroke-linejoin="round">
        <path d="M30 20 l6 6 l-10 10 l-6 -6 z"/>
        <path d="M22 34 l-6 6 M18 38 l-2 2"/>
        <path d="M34 16 a6 6 0 0 1 6 6 M36 11 a11 11 0 0 1 9 9"/>
      </svg>
    </div>
    Our Screening Uses TCD<br>a Form of Ultrasound.
  </section>

  <section class="hero">
    <svg class="hero__art" width="848" height="580" viewBox="0 460 848 580">
      <path d="M520 545 C690 545 800 660 800 800 C800 880 770 940 722 985" fill="none" stroke="var(--swoosh-light)" stroke-width="72" stroke-linecap="round"/>
      <path d="M170 490 C115 560 60 680 60 805 C60 945 200 1028 360 1028 C490 1028 590 990 640 950 C662 932 648 895 615 905 C555 928 470 948 400 930 L340 910 L340 720 C270 660 186 600 186 505 C186 478 180 478 170 490 Z" fill="var(--swoosh-blue)"/>
    </svg>
    <div class="hero__brain" role="img" aria-label="Network-style illustration of a brain made of connected dots"></div>
    <div class="hero__child" role="img" aria-label="Photo of a smiling child in a yellow sweater with both arms raised in celebration"></div>
  </section>

  <div class="why-tag">WHY?</div>
  <p class="why-copy">
    <span style="margin-left:85px">Nearly 11%</span>
    <span style="margin-left:87px">of patients</span>
    <span style="margin-left:91px">with SCD</span>
    <span style="margin-left:96px">will experi-</span>
    <span style="margin-left:101px">ence a stroke</span>
    <span style="margin-left:109px">before the</span>
    <span style="margin-left:118px">age of 20, with</span>
    <span style="margin-left:129px">the highest risk</span>
    <span style="margin-left:141px">between</span>
  </p>
  <div class="age-label">AGE</div>
  <div class="age-pill">
    <div class="age-pill__range">2 TO 5</div>
    <div class="age-pill__unit">YEARS OLD.</div>
  </div>

  <section class="closing">
    <p class="closing__line">SCREENING FOR EARLY SIGNS OF STROKE CAN BE A TOOL FOR EARLY DIAGNOSIS.</p>
    <p class="closing__cta">ALLOWING FOR TREATMENTS THAT ELIMINATE THE RISK.</p>
  </section>

  <footer class="footer">
    <span class="footer__call">CALL TO SCHEDULE</span>
    <svg class="footer__arrow" width="22" height="22" viewBox="0 0 22 22">
      <circle cx="11" cy="11" r="10" fill="var(--title-navy)" stroke="#fff" stroke-width="1.5"/>
      <path d="M7 7 l4 4 l-4 4 M11 7 l4 4 l-4 4" fill="none" stroke="#fff" stroke-width="1.8" stroke-linecap="round" stroke-linejoin="round"/>
    </svg>
    <span class="footer__web">BRIGHTPATHWELLBEING.NET</span>
  </footer>
  <div class="footer__phone-box">833-412-7086</div>

  <div class="stripe stripe--bottom"><span></span><span></span><span></span><span></span><span></span><span></span><span></span><span></span><span></span><span></span><span></span><span></span><span></span><span></span></div>
</main>
</body>
</html>
```